Contemporary Business card for Event Manager

Needed for my startup events company in Melbourne. Events I manage will be based within the fashion industry, sporting events, product launches etc. Not weddings or small dinner parties. Therfore I am after something professional and aimed at high end corporate market; but with the added emphasis on not being too conservative or boring. I am happy with a pop of colour e.g. yellow or copper foil.

Target Market(s)

fashion industry, design industry, high end sporting events e.g. Polo, Grand Prix, corporate clients,

Industry/Entity Type

Fashion

Contact Information for Business Card

side 1
Lucy Brandt (can be upper or lower case, have a feature full stop between first and surname, or at the end of the nameetc) I am open to ideas. I would also be fine with my initials or name as a logo on the front (if this is the case my full name would need to go on the second side of the card.
2nd side:
Mobile: +61 400 817 263
email: lucy.brandt@mailnest.com.au

on one side of the card:
event management | brand activation | Advisory Services

Font styles to use
Serif
Sans Serif

Requirements
Must have
• side 2 must have
• mobile number
• email address
• event management | brand activation | Advisory Services
• ** my full name (Lucy Brandt) must be on the card somewhere)
Nice to have
• 1st side
• I see the card stock being either a dark grey, light grey, natural white or black (all matt colours on unprocessed card). I see the writing being copper foil, or foil white or foil black.
• To give you a feel for me, think: contemporary, minimalist, I love line drawings, concrete, white with grey vein marble, copper, white, grey, black...yes I do like colour....yellow (but pops of colour) ;) I would like the card to look designer but 'on trend' as I deal with a lot of design and fashion clients....styles - think the sophistication and simplicity of Vireaux or urban contemporary.
• some examples of what I like. Although please don't leet this limit you...I really am happy to have something a little more urban or design focused like a line drawing of an object, person too or a photo image too.
• https://www.moodtackle.com/pin/830165427719302846/
• https://www.moodtackle.com/pin/607281935540173268/
• https://www.moodtackle.com/pin/318746205913457092/
• https://www.moodtackle.com/pin/41983627530918476/
• https://www.moodtackle.com/pin/53128940672419087/
• https://www.moodtackle.com/pin/90316284750638152/
• https://www.moodtackle.com/pin/734092618450362918/
• https://www.moodtackle.com/pin/926354081736215407/
• https://www.moodtackle.com/pin/481627093518704356/
Should not have
• should not look commercial or have cartoonish looking logos. However happy with a simple line drawing or logo with initials etc.

```html
<!DOCTYPE html>
<html lang="en">
<head>
<meta charset="utf-8">
<title>Lucy Brandt — Business Card</title>
<link rel="stylesheet" href="https://fonts.googleapis.com/css2?family=Quicksand:wght@300;400&display=swap">
<style>
  :root {
    --canvas: #e9e7e3;
    --card-black: #1c1d1f;
    --paper: #f7f7f5;
    --teal: #22c2c9;
    --teal-deep: #1aa9b0;
    --ink-white: #f2f2f2;
    --ornament: #3a3a3a;
  }
  * { box-sizing: border-box; margin: 0; padding: 0; }
  html, body { width: 1200px; height: 902px; overflow: hidden; }
  body {
    background: var(--canvas);
    font-family: "Quicksand", sans-serif;
    font-weight: 300;
    position: relative;
  }
  .card {
    position: absolute;
    left: 320px;
    width: 560px;
    height: 320px;
    border-radius: 6px;
    overflow: hidden;
    background: var(--card-black);
    box-shadow: 0 10px 28px rgba(0,0,0,0.22);
  }
  .card--front { top: 90px; }
  .card--back { top: 480px; }

  /* front */
  .front-panel {
    position: absolute;
    left: 48px; right: 42px;
    top: 64px; height: 150px;
    background: var(--paper);
    display: flex;
    align-items: center;
    justify-content: center;
    gap: 18px;
  }
  .ornament {
    flex: none;
    width: 30px; height: 30px;
    border-radius: 4px;
    background: var(--ornament);
  }
  .name {
    color: var(--teal);
    font-size: 40px;
    font-weight: 300;
    line-height: 1;
    letter-spacing: 0.5px;
  }

  /* back */
  .back-panel {
    position: absolute;
    left: 0; right: 0; top: 0; height: 160px;
    background: var(--paper);
    display: flex;
    align-items: flex-end;
    justify-content: center;
    padding-bottom: 34px;
  }
  .services {
    list-style: none;
    color: var(--teal);
    font-size: 15px;
    font-weight: 300;
    line-height: 1.2;
  }
  .services li:nth-child(2) { padding-left: 20px; }
  .services li:nth-child(3) { padding-left: 40px; }
  .contact {
    position: absolute;
    left: 250px; top: 192px;
    color: var(--ink-white);
    font-size: 16px;
    font-style: normal;
    font-weight: 300;
    line-height: 1.35;
  }
  .contact .phone { padding-left: 14px; }
  .accent-strip {
    position: absolute;
    left: 0; right: 0; bottom: 0; height: 18px;
    background: linear-gradient(to bottom, var(--teal), var(--teal-deep));
  }
</style>
</head>
<body>
  <section class="card card--front" aria-label="Card front">
    <div class="front-panel">
      <div class="ornament" role="img" aria-label="Decorative black flourish"></div>
      <h1 class="name">Lucy Brandt</h1>
      <div class="ornament" role="img" aria-label="Decorative black flourish"></div>
    </div>
  </section>

  <section class="card card--back" aria-label="Card back">
    <div class="back-panel">
      <ul class="services">
        <li>event management</li>
        <li>brand activation</li>
        <li>Advisory Services</li>
      </ul>
    </div>
    <address class="contact">
      <div class="phone">+61 400 817 263</div>
      <div class="email">lucy.brandt@mailnest.com.au</div>
    </address>
    <div class="accent-strip"></div>
  </section>
</body>
</html>
```